PitchTally Webpages and Logo

See attached brief. Take the existing website www.pitchtally.co.uk and logo and transform these assets to:

Give people who arrive on the site for first time the confidence to sign-up easily and quickly
Allow regular returning users quick and easy placing of predictions and encourage them to share the PitchTally prediction on social networks and with their contacts
Convey the essence of a community working together to enjoyably come-up with smart predictions on sporting events
Work seamlessly and well across smartphones, tablets and desktop i.e. Should be Responsive Web Design
Updates

Target Market(s)

Users are sports fans with opinions
Primarily male and early twenties to mid-thirties
They are competitive - they want to beat their peers
Many are from outside the UK

Industry/Entity Type

Events

Logo Text

PitchTally

Coding

Coded - Design and coding required

Number of Pages Required

4 page

Font styles to use
Sans Serif

Requirements
Must have
• Responsive Web Design
• Mobile First
• HTML must work with dedicated bespoke application developed in ASP.NET using MS SQL underneath
• See Brief
Nice to have
• See brief
Should not have
• See brief

```html
<!DOCTYPE html>
<html lang="en">
<head>
<meta charset="utf-8">
<title>PitchTally – Altogether Better Predictions</title>
<link href="https://fonts.googleapis.com/css2?family=Bebas+Neue&family=Open+Sans:wght@300;400;600;700;800&display=swap" rel="stylesheet">
<style>
:root{
  --nav:#2f2f31;
  --band:#363638;
  --teal:#1fa592;
  --teal-dark:#17917f;
  --blue:#5aa6d6;
  --gold:#d9b44a;
  --card:#f2f2f2;
  --card-line:#e3e3e3;
  --ink:#222;
  --muted:#555;
  --white:#fff;
  --fb:#3e5a9a;
}
*{box-sizing:border-box;margin:0;padding:0}
html,body{width:802px;height:1200px;overflow:hidden;background:var(--white)}
body{position:relative;font-family:"Open Sans",Arial,sans-serif;color:var(--ink)}
.display{font-family:"Bebas Neue",Impact,sans-serif;font-weight:400}

/* header */
.site-header{position:absolute;left:0;top:0;width:802px;height:43px;background:var(--nav)}
.brand{position:absolute;left:40px;top:11px;display:flex;align-items:center;gap:6px;color:var(--white);font-weight:800;font-size:13px}
.brand-dot{width:18px;height:18px;border-radius:50%;background:var(--teal)}
.main-nav a{position:absolute;top:11px;height:22px;line-height:22px;font-size:9px;color:var(--white);text-decoration:none;font-weight:600}
.main-nav .active{left:171px;width:54px;text-align:center;border-radius:11px;background:var(--teal)}
.sign-in{position:absolute;left:595px;top:11px;width:60px;height:22px;line-height:22px;border-radius:11px;background:var(--blue);color:var(--white);font-size:8.5px;font-weight:700;text-align:center}
.search{position:absolute;left:662px;top:11px;width:98px;height:22px;border-radius:11px;background:#222224;color:#888;font-size:8.5px;line-height:22px;padding-left:21px}
.search svg{position:absolute;left:8px;top:6px}

/* hero */
.hero{position:absolute;left:0;top:43px;width:802px;height:402px;background:linear-gradient(160deg,#5e6064 0%,#3b3d42 45%,#2a2c33 100%);color:var(--white);text-align:center}
.hero-photo{position:absolute;inset:0;background:radial-gradient(ellipse at 40% 40%,rgba(200,200,200,.35),transparent 55%),radial-gradient(ellipse at 70% 55%,rgba(60,80,140,.45),transparent 50%)}
.hero h1{position:absolute;left:0;width:802px;top:34px;font-size:38px;letter-spacing:1px}
.hero-lead{position:absolute;left:166px;width:470px;top:95px;font-size:14px;line-height:21px}
.join{position:absolute;left:352px;top:180px;width:98px;height:29px;line-height:29px;border-radius:15px;background:var(--teal);font-size:11px;font-weight:700}
.feature{position:absolute;top:246px;width:240px;text-align:center}
.feature-icon{width:59px;height:59px;border-radius:50%;margin:0 auto;display:flex;align-items:center;justify-content:center}
.feature h2{font-size:28px;margin-top:7px;line-height:28px}
.feature p{font-size:11px;line-height:14px;margin-top:3px}

/* tips band */
.tips-band{position:absolute;left:0;top:445px;width:802px;height:60px;background:var(--band)}
.tips-band h2{position:absolute;left:50px;top:14px;font-size:27px;color:var(--white);letter-spacing:.3px}
.share{position:absolute;top:16px;width:178px;height:26px;border-radius:3px;color:var(--white);font-size:10.5px;font-weight:700;display:flex}
.share .ico{width:28px;height:26px;border-right:1px solid rgba(0,0,0,.15)}
.share .label{flex:1;text-align:center;line-height:26px}
.share.friendbook{left:265px;background:var(--fb)}
.share.chirper{left:469px;background:var(--blue)}

/* stats */
.stat{position:absolute;top:536px;width:240px;text-align:center}
.stat h3{font-size:20px;margin-top:4px;line-height:20px}
.stat .pct{font-weight:700;font-size:28px;line-height:32px;margin-top:3px}
.stat p{font-size:10.5px;line-height:12px;margin-top:4px;text-transform:uppercase}

/* fixture cards */
.card{position:absolute;width:222px;height:166px;background:var(--card);border:1px solid var(--card-line)}
.teams{position:absolute;left:12px;right:14px;top:10px;display:flex;justify-content:space-between;font-size:11.5px;color:var(--muted)}
.crest{position:absolute;top:36px;width:54px;height:60px;border-radius:50%}
.crest.home{left:19px;background:#c8202f}
.crest.away{right:19px;top:38px;background:var(--gold)}
.vs{position:absolute;left:0;right:0;top:52px;text-align:center;font-size:27px;color:#444;font-weight:300}
.kickoff{position:absolute;left:0;right:0;top:113px;text-align:center;font-size:8.5px;color:var(--muted)}
.predict{position:absolute;left:25px;top:129px;width:172px;height:24px;line-height:24px;text-align:center;background:var(--teal);color:var(--white);font-size:10.5px;border:1px solid var(--teal-dark)}
.card.tipster{overflow:hidden}
.tipster-photo{position:absolute;right:0;top:10px;width:78px;height:156px;background:linear-gradient(180deg,#e9c2a4,#b88363 60%,#2a2a2a)}
.tipster-copy{position:absolute;left:24px;top:44px;width:122px;font-size:12px;line-height:16.5px;color:#444;font-weight:300}
.see{position:absolute;left:24px;top:129px;width:172px;height:24px;line-height:24px;text-align:center;background:var(--blue);color:var(--white);font-size:10.5px}

/* footer */
.site-footer{position:absolute;left:0;top:1083px;width:802px;height:117px;background:var(--band);color:var(--white);text-align:center}
.footer-links{position:absolute;left:0;width:802px;top:21px;display:flex;justify-content:center;gap:20px;font-size:10px}
.social{position:absolute;left:0;width:802px;top:51px;display:flex;justify-content:center;gap:13px}
.social span{width:22px;height:22px;border-radius:50%;background:#5d5d61}
.copy{position:absolute;left:0;width:802px;top:93px;font-size:8px;color:#aaa}
</style>
</head>
<body>

<header class="site-header">
  <div class="brand"><span class="brand-dot"></span>PitchTally</div>
  <nav class="main-nav">
    <a class="active">HOME</a>
    <a style="left:241px">MINILIGA</a>
    <a style="left:308px">TABLES</a>
    <a style="left:366px">KITTY</a>
    <a style="left:418px">FAQ</a>
    <a style="left:465px">ME</a>
  </nav>
  <div class="sign-in">Sign in &#709;</div>
  <div class="search"><svg width="9" height="9" viewBox="0 0 10 10"><circle cx="4" cy="4" r="3" fill="none" stroke="#888" stroke-width="1.3"/><line x1="6.3" y1="6.3" x2="9" y2="9" stroke="#888" stroke-width="1.3"/></svg>Search</div>
</header>

<section class="hero">
  <div class="hero-photo" role="img" aria-label="Two footballers leaping for the ball in a stadium"></div>
  <h1 class="display">Altogether Better Predictions</h1>
  <p class="hero-lead">Predict results, scores and scorers for your free chance to win a £20 ShopMart voucher every week. Overall season winner gets up to £1000 in ShopMart vouchers! No entry fee and no catches.</p>
  <div class="join">JOIN NOW</div>

  <div class="feature" style="left:39px">
    <div class="feature-icon" style="background:var(--teal)">
      <svg width="30" height="30" viewBox="0 0 30 30"><path d="M8 27v-6c-3-2-4-5-4-8a11 11 0 0 1 22 0l3 5h-3v4a3 3 0 0 1-3 3h-3v2z" fill="#fff"/><circle cx="12" cy="12" r="1.6" fill="#1fa592"/><circle cx="16" cy="12" r="1.6" fill="#1fa592"/><circle cx="20" cy="12" r="1.6" fill="#1fa592"/></svg>
    </div>
    <h2 class="display">Predict</h2>
    <p>The scores from the 5 matches this weekend</p>
  </div>
  <div class="feature" style="left:281px">
    <div class="feature-icon" style="background:var(--blue)">
      <svg width="30" height="30" viewBox="0 0 30 30"><rect x="4" y="10" width="22" height="6" fill="#fff"/><rect x="6" y="16" width="18" height="11" fill="#e9615a"/><rect x="13" y="10" width="4" height="17" fill="#fff"/><path d="M15 10c-3-6-8-5-7-2s7 2 7 2c0 0 6 1 7-2s-4-4-7 2z" fill="#fff"/></svg>
    </div>
    <h2 class="display">Get Tips</h2>
    <p>Based on the wisdom of the crowd</p>
  </div>
  <div class="feature" style="left:522px">
    <div class="feature-icon" style="background:var(--gold)">
      <svg width="30" height="30" viewBox="0 0 30 30"><path d="M9 4h12v7a6 6 0 0 1-12 0z" fill="#fff"/><path d="M9 6H4c0 5 3 7 6 7M21 6h5c0 5-3 7-6 7" fill="none" stroke="#fff" stroke-width="2"/><rect x="13.5" y="16" width="3" height="6" fill="#fff"/><rect x="9" y="22" width="12" height="4" fill="#fff"/></svg>
    </div>
    <h2 class="display">Enjoy</h2>
    <p>The glory of being a top tipster and scooping the jackpot!</p>
  </div>
</section>

<section class="tips-band">
  <h2 class="display">Tips From The Crowd</h2>
  <div class="share friendbook"><span class="ico"></span><span class="label">Share on Friendbook</span></div>
  <div class="share chirper"><span class="ico"></span><span class="label">Share on Chirper</span></div>
</section>

<section class="stats">
  <div class="stat" style="left:40px">
    <svg width="36" height="36" viewBox="0 0 36 36"><path d="M6 2h8l4 10 4-10h8l-9 16h-6z" fill="#1fa592"/><circle cx="18" cy="24" r="11" fill="#d9b44a"/><path d="M18 17l2.1 4.4 4.8.6-3.5 3.3.9 4.7-4.3-2.3-4.3 2.3.9-4.7-3.5-3.3 4.8-.6z" fill="#f6de8a"/></svg>
    <h3 class="display">Result</h3>
    <div class="pct" style="color:var(--teal)">100%</div>
    <p>Thames Ironside win</p>
  </div>
  <div class="stat" style="left:281px">
    <svg width="36" height="36" viewBox="0 0 36 36"><path d="M6 2h8l4 10 4-10h8l-9 16h-6z" fill="#1fa592"/><circle cx="18" cy="24" r="11" fill="#d9b44a"/><path d="M18 17l2.1 4.4 4.8.6-3.5 3.3.9 4.7-4.3-2.3-4.3 2.3.9-4.7-3.5-3.3 4.8-.6z" fill="#f6de8a"/></svg>
    <h3 class="display">Score</h3>
    <div class="pct" style="color:var(--blue)">100%</div>
    <p>Midland Claret 0 Irwell<br>United 2</p>
  </div>
  <div class="stat" style="left:524px">
    <svg width="36" height="36" viewBox="0 0 36 36"><path d="M6 2h8l4 10 4-10h8l-9 16h-6z" fill="#1fa592"/><circle cx="18" cy="24" r="11" fill="#d9b44a"/><path d="M18 17l2.1 4.4 4.8.6-3.5 3.3.9 4.7-4.3-2.3-4.3 2.3.9-4.7-3.5-3.3 4.8-.6z" fill="#f6de8a"/></svg>
    <h3 class="display">1st Goal</h3>
    <div class="pct" style="color:var(--gold)">57%</div>
    <p>Barlow C</p>
  </div>
</section>

<section class="fixtures">
  <article class="card" style="left:48px;top:693px">
    <div class="teams"><span>Mersey Rovers</span><span>Castilla Royal</span></div>
    <div class="crest home"></div><div class="vs">VS</div><div class="crest away"></div>
    <div class="kickoff">14 October 2013, 23:00 (FT)</div>
    <div class="predict">PREDICT SCORE NOW</div>
  </article>
  <article class="card" style="left:290px;top:693px">
    <div class="teams"><span>Mersey Rovers</span><span>Castilla Royal</span></div>
    <div class="crest home"></div><div class="vs">VS</div><div class="crest away"></div>
    <div class="kickoff">14 October 2013, 23:00 (FT)</div>
    <div class="predict">PREDICT SCORE NOW</div>
  </article>
  <article class="card" style="left:530px;top:693px">
    <div class="teams"><span>Mersey Rovers</span><span>Castilla Royal</span></div>
    <div class="crest home"></div><div class="vs">VS</div><div class="crest away"></div>
    <div class="kickoff">14 October 2013, 23:00 (FT)</div>
    <div class="predict">PREDICT SCORE NOW</div>
  </article>
  <article class="card" style="left:48px;top:878px">
    <div class="teams"><span>Mersey Rovers</span><span>Castilla Royal</span></div>
    <div class="crest home"></div><div class="vs">VS</div><div class="crest away"></div>
    <div class="kickoff">14 October 2013, 23:00 (FT)</div>
    <div class="predict">PREDICT SCORE NOW</div>
  </article>
  <article class="card" style="left:290px;top:878px">
    <div class="teams"><span>Mersey Rovers</span><span>Castilla Royal</span></div>
    <div class="crest home"></div><div class="vs">VS</div><div class="crest away"></div>
    <div class="kickoff">14 October 2013, 23:00 (FT)</div>
    <div class="predict">PREDICT SCORE NOW</div>
  </article>
  <article class="card tipster" style="left:530px;top:878px">
    <div class="tipster-photo" role="img" aria-label="Smiling tipster portrait"></div>
    <p class="tipster-copy">See how Mr Numbers<br>got on with your<br>predictions last<br>week</p>
    <div class="see">SEE THE PREDICTION</div>
  </article>
</section>

<footer class="site-footer">
  <nav class="footer-links"><span>About</span><span>Terms</span><span>Site Map</span><span>Privacy</span><span>Contact Us</span></nav>
  <div class="social"><span></span><span></span><span></span><span></span><span></span></div>
  <p class="copy">© PitchTally 2014 – All Right Reserved</p>
</footer>

</body>
</html>
```